Business Card for Professional Photographer

I'm looking for an eye catching modern clean design that compliments my logo/ website fonts & colours.
I specialise in architecture, corporate & commercial photography so I'm marketing to professional clients rather than portrait / wedding clients.

I would prefer to not have a solid black design.

My logo brand guide is as follows :

Main front font. : Reislust
Main font colour : #fff
Slogan front font : Ubuntu Bold
Monogram front font : Venti Medium
Container colour : #fff

I need print ready files in pdf .png & .eps formats.

Included in the files below are some screen grabs as reference to font & colours etc.

```html
<!DOCTYPE html>
<html lang="en">
<head>
<meta charset="utf-8">
<title>Angle of Light – Business Card</title>
<link rel="stylesheet" href="https://fonts.googleapis.com/css2?family=Jost:wght@300&family=Ubuntu:wght@400;700&family=Saira+Condensed:wght@600&family=Roboto:wght@400&display=swap">
<style>
  :root {
    --backdrop: #b9b9b9;
    --gold-dark: #b8893e;
    --gold-mid: #d4b66a;
    --gold-light: #ebe09f;
    --gold-text: #b08646;
    --ink: #1c1c1c;
    --ink-soft: #333333;
    --card-white: #f7f7f6;
  }
  * { box-sizing: border-box; margin: 0; padding: 0; }
  html, body {
    width: 1200px; height: 576px; overflow: hidden;
    background: var(--backdrop);
  }
  .canvas { position: relative; width: 1200px; height: 576px; }

  .card {
    position: absolute; top: 138px;
    width: 484px; height: 294px;
    border-radius: 12px; overflow: hidden;
  }

  /* Front */
  .card-front {
    left: 82px;
    background: linear-gradient(35deg, var(--gold-dark) 0%, var(--gold-mid) 45%, var(--gold-light) 100%);
  }
  .front-mark {
    position: absolute; left: 74px; top: 118px;
    width: 56px; height: 56px; border-radius: 50%;
    background: var(--ink);
  }
  .front-brand { position: absolute; left: 182px; top: 122px; }
  .brand-name {
    font-family: "Jost", sans-serif; font-weight: 300;
    font-size: 23px; letter-spacing: 3px; line-height: 1;
    text-transform: uppercase; white-space: nowrap;
  }
  .brand-tagline {
    font-family: "Ubuntu", sans-serif; font-weight: 700;
    font-size: 7.5px; letter-spacing: 1.6px; white-space: nowrap;
    margin-top: 6px;
  }
  .front-brand .brand-name, .front-brand .brand-tagline { color: var(--ink); }
  .front-web {
    position: absolute; left: 0; right: 0; top: 256px; text-align: center;
    font-family: "Ubuntu", sans-serif; font-size: 13px; letter-spacing: 2.2px;
    color: var(--ink-soft);
  }

  /* Back */
  .card-back { left: 601px; background: var(--card-white); }
  .back-brand {
    position: absolute; left: 38px; top: 172px; width: 190px; text-align: center;
  }
  .back-brand .brand-name { color: var(--gold-text); font-size: 19px; letter-spacing: 2.4px; }
  .back-brand .brand-tagline { color: var(--gold-text); font-size: 6px; letter-spacing: 1.3px; margin-top: 5px; }

  .person { position: absolute; left: 269px; top: 84px; }
  .person-name {
    font-family: "Saira Condensed", sans-serif; font-weight: 600;
    font-size: 20px; color: var(--gold-text); line-height: 1;
  }
  .person-role {
    font-family: "Roboto", sans-serif; font-size: 12.5px; color: var(--ink-soft);
    margin-top: 5px;
  }
  .contact-list { position: absolute; left: 272px; top: 130px; list-style: none; }
  .contact-item {
    display: flex; align-items: center; gap: 10px; height: 18.5px;
    font-family: "Roboto", sans-serif; font-size: 12.5px; color: var(--ink-soft);
  }
  .contact-icon { width: 9px; height: 9px; flex: none; }

  .back-band { position: absolute; left: 0; top: 0; }
  .address {
    position: absolute; left: 236px; right: 0; top: 266px; text-align: center;
    font-family: "Roboto", sans-serif; font-size: 12.5px; color: var(--ink);
  }
</style>
</head>
<body>
<main class="canvas">
  <section class="card card-front" aria-label="Card front">
    <span class="front-mark" aria-hidden="true"></span>
    <div class="front-brand">
      <p class="brand-name">Angle of Light</p>
      <p class="brand-tagline">Architecture Corporate Commercial</p>
    </div>
    <p class="front-web">www.angleoflight.com.au</p>
  </section>

  <section class="card card-back" aria-label="Card back">
    <svg class="back-band" width="484" height="294" viewBox="0 0 484 294" aria-hidden="true">
      <defs>
        <linearGradient id="bandGold" x1="0" y1="0" x2="1" y2="0">
          <stop offset="0" stop-color="#b8893e"/>
          <stop offset="0.55" stop-color="#d9c07a"/>
          <stop offset="1" stop-color="#ebe09f"/>
        </linearGradient>
      </defs>
      <path d="M0 280 H210 L228 256 H484 V294 H0 Z" fill="url(#bandGold)"/>
    </svg>

    <div class="back-brand">
      <p class="brand-name">Angle of Light</p>
      <p class="brand-tagline">Architecture Corporate Commercial</p>
    </div>

    <div class="person">
      <p class="person-name">Reid Morgan</p>
      <p class="person-role">Photographer</p>
    </div>

    <ul class="contact-list">
      <li class="contact-item">
        <svg class="contact-icon" viewBox="0 0 10 10" aria-hidden="true"><path d="M2 1 L4 1 L4.6 3 L3.5 3.8 Q4.5 5.8 6.2 6.5 L7 5.4 L9 6 L9 8 Q8.6 9 7.5 9 Q1 8 1 2.5 Q1 1 2 1 Z" fill="#b08646"/></svg>
        <span>0412555018</span>
      </li>
      <li class="contact-item">
        <svg class="contact-icon" viewBox="0 0 10 10" aria-hidden="true"><rect x="0.5" y="2" width="9" height="6.5" fill="#b08646"/><path d="M0.5 2 L5 5.6 L9.5 2" fill="none" stroke="#f7f7f6" stroke-width="0.9"/></svg>
        <span>info@angleoflight.com.au</span>
      </li>
      <li class="contact-item">
        <svg class="contact-icon" viewBox="0 0 10 10" aria-hidden="true"><circle cx="5" cy="5" r="4.3" fill="none" stroke="#b08646" stroke-width="1"/><ellipse cx="5" cy="5" rx="1.8" ry="4.3" fill="none" stroke="#b08646" stroke-width="0.8"/><path d="M0.7 5 H9.3" stroke="#b08646" stroke-width="0.8"/></svg>
        <span>www.angleoflight.com.au</span>
      </li>
    </ul>

    <p class="address">48 Harbour Rd Ashby Vic 3270</p>
  </section>
</main>
</body>
</html>
```